Las Vegas Tour guide needs website of future for physical and selfguided assets

Neon Drifters is the parent site to my Las Vegas tour operation. Within this is a physical walking tour called Whispers and the Racket, the site traffic driver where I tell history with a paranormal twist. The legacy site can be seen at spookyroutewalks.com.
The Neon Drifters app has self guided tours called Desert Hop Trail/Whispers and The Racket Retold/Calloway Row Stroll. Rivano is a 3rd party tour company I have partnered with to sale self-guided tours with a scavenger hunt theme.
I like black and pink and pistachio green colors however am flexible in theme. Colors should follow Vegas 50-60s aesthetics. The “Greetings From Silver Gulch Marker” should not be considered as design inspiration. 95% of traffic is on mobile. Final design should be easy to understand guided versus self-guided option. Show cross promotion links for digital assets/physical tour. Rivano content tbd by end of week 9 Aug 2021
sites i like
nationalspiritstrolls.com
heronsandshades.com
oldportphantomtrips.net
Updates

Needs a book now at top, or floating like lorvantrips. Less busy and stay away from using photos. I have included more websites for inspiration. I would like a mashup of the two sites eerieechoplace and lorvantrips. I am unsure what some of your designs would look like on a mobile screen. Please screenshot that. https://eerieechoplace.com/ https://www.lorvantrips.com/ https://k7vrx.com/ https://bqspecters.com/ https://bluefinjaunts.com/tours/new-york-city/shades-of-pellham-corner/

Family member hospitalized need extra time to review

Target Market(s)

Tourist 25+

Industry/Entity Type

Travel. Tour guide.

Coding

Coded - Design and coding required

Number of Pages Required

5+ page

Font styles to use
Serif

Colors
00AB8E
00BBA5
67D7C9
C6EFE9
E9F9F6
59FF00
82FF00
B8FF75
E3FFCB
F4FFEA
EB3D1F
EC4F4E
F09395
F8D3D4
FCEDEE
E54698
E96AAD
F1A4CE
F9D9EA
FCEFF6

Requirements
Must have
• Cross promotion between physical tour and digital
Nice to have
• sliver button like ads as breaks between tour info
Should not have
• "Greetings from Silver Gulch Marker". no photos. no animation.

```html
<!DOCTYPE html>
<html lang="en">
<head>
<meta charset="utf-8">
<title>Whispers and The Racket Las Vegas Walking Tour</title>
<link href="https://fonts.googleapis.com/css2?family=Lora:wght@400;700&display=swap" rel="stylesheet">
<style>
:root{
  --page:#f6b9d5;
  --pink:#e54698;
  --pink-soft:#e96aad;
  --green:#9acd5c;
  --dark:#2a2a2a;
  --darker:#1d1d1d;
  --rule:#5a5a5a;
  --white:#ffffff;
  --text-soft:#d9d9d9;
  --map-a:#efe6cf;
  --map-b:#d9e6c6;
}
*{box-sizing:border-box;margin:0;padding:0}
html,body{width:707px;height:1200px;overflow:hidden}
body{background:var(--page);font-family:"Lora",Georgia,serif;position:relative}
.screen{position:absolute;background:var(--dark);overflow:hidden;display:flex;flex-direction:column;box-shadow:0 2px 6px rgba(0,0,0,.15)}
.desktop{left:12px;top:12px;width:471px;height:1178px}
.mobile{left:502px;top:12px;width:193px;height:895px}

.site-header{background:var(--white);display:flex;align-items:center;justify-content:space-between;padding:0 14px;flex:none}
.desktop .site-header{height:35px}
.mobile .site-header{height:35px;flex-direction:column;justify-content:center;gap:2px}
.brand{display:flex;align-items:center;gap:4px;font-weight:700;color:var(--pink);font-size:10px}
.brand-dot{width:10px;height:10px;border-radius:50%;background:var(--green)}
.phone{color:var(--pink);font-weight:700;font-size:10px;display:flex;align-items:center;gap:3px}
.mobile .phone{font-size:8px}
.phone svg{width:8px;height:8px}
.socials{display:flex;gap:3px}
.socials span{width:7px;height:7px;border-radius:50%;background:#8a8a8a}

.main-nav{background:var(--green);display:flex;justify-content:center;align-items:center;gap:10px;flex:none}
.desktop .main-nav{height:17px}
.mobile .main-nav{height:19px;flex-wrap:wrap;gap:1px 6px;padding:2px 6px}
.main-nav a{color:var(--white);font-size:5px;font-weight:700;text-decoration:none;text-transform:uppercase;letter-spacing:.2px}

.hero{background:linear-gradient(160deg,#3b3550 0%,#6b5346 45%,#2d2a33 100%);display:flex;flex-direction:column;align-items:center;justify-content:center;text-align:center;color:var(--white);flex:none}
.desktop .hero{height:184px;gap:14px}
.mobile .hero{height:111px;gap:8px;padding:0 10px}
.hero h1{font-weight:700;line-height:1.2;text-shadow:0 1px 3px rgba(0,0,0,.5)}
.desktop .hero h1{font-size:19px}
.mobile .hero h1{font-size:11px}

.btn{display:inline-block;background:var(--pink);color:var(--white);font-weight:700;text-decoration:none;border-radius:2px}
.desktop .btn{font-size:7px;padding:6px 12px}
.mobile .btn{font-size:6px;padding:4px 9px}

.welcome{text-align:center;color:var(--white);display:flex;flex-direction:column;align-items:center;flex:none}
.desktop .welcome{height:236px;padding:34px 40px 0;gap:12px}
.mobile .welcome{height:118px;padding:14px 12px 0;gap:7px}
.section-title{font-weight:700;color:var(--white);line-height:1.25}
.desktop .section-title{font-size:13px}
.mobile .section-title{font-size:9.5px}
.body-text{color:var(--text-soft);line-height:1.6}
.desktop .body-text{font-size:6px}
.mobile .body-text{font-size:5px}

.rule{height:1px;background:var(--rule);flex:none}
.desktop .rule{margin:0 24px}
.mobile .rule{margin:0 12px}

.feature{display:flex;align-items:center;flex:none}
.desktop .feature{gap:18px;padding:0 24px}
.desktop .explore{height:212px}
.desktop .details{height:224px}
.mobile .feature{flex-direction:column;align-items:stretch;padding:0 12px 12px;gap:8px}
.mobile .explore{height:212px}
.mobile .details{height:184px;padding-top:12px}
.feature-copy{display:flex;flex-direction:column;gap:10px}
.desktop .feature-copy{flex:1}
.map{background:linear-gradient(135deg,var(--map-a),var(--map-b));border:2px solid var(--white);flex:none}
.desktop .map{width:205px;height:150px}
.mobile .map{width:100%;height:62px}
.mobile .explore .section-title{background:var(--pink-soft);padding:7px 8px;margin:0 -12px}
.ticks{list-style:none;display:flex;flex-direction:column;gap:6px}
.ticks li{display:flex;gap:5px;align-items:flex-start;color:var(--text-soft);line-height:1.5}
.desktop .ticks li{font-size:6px}
.mobile .ticks li{font-size:5px}
.ticks svg{width:6px;height:6px;flex:none;margin-top:1px}
.desktop .details .btn{align-self:flex-start}
.mobile .details .btn{align-self:center}

.app-promo{background:var(--green);display:flex;align-items:center;flex:none}
.desktop .app-promo{height:118px;padding:0 24px;justify-content:space-between}
.mobile .app-promo{height:83px;flex-direction:column;justify-content:center;gap:6px;padding:0 10px;text-align:center}
.app-promo h2{font-weight:700;color:var(--darker);line-height:1.3}
.desktop .app-promo h2{font-size:12.5px;width:240px}
.mobile .app-promo h2{font-size:8px}
.store-badges{display:flex;gap:5px}
.desktop .store-badges{flex-direction:column}
.store-badges span{background:var(--darker);border-radius:4px;display:block}
.desktop .store-badges span{width:84px;height:24px}
.mobile .store-badges span{width:52px;height:15px}

.site-footer{background:var(--darker);color:var(--text-soft);display:flex;flex-direction:column;align-items:center;justify-content:center;flex:1;gap:8px;text-align:center}
.footer-links{display:flex;flex-wrap:wrap;justify-content:center;gap:4px 12px;padding:0 20px}
.footer-links a{color:var(--white);text-decoration:none;font-size:5px;font-weight:700;text-transform:uppercase}
.mobile .footer-links{flex-direction:column;gap:4px}
.copyright{font-size:4.5px;color:#9a9a9a}
</style>
</head>
<body>

<section class="screen desktop">
  <header class="site-header">
    <div class="brand"><span class="brand-dot"></span>Neon Drifters</div>
    <div class="phone"><svg viewBox="0 0 10 10"><path d="M2 1l2 2-1 1.2a6 6 0 0 0 2.8 2.8L7 6l2 2-1.3 1.3C4.5 9 1 5.5.7 2.3z" fill="#e54698"/></svg>(702) 555-0148</div>
    <div class="socials"><span></span><span></span><span></span><span></span><span></span><span></span></div>
  </header>
  <nav class="main-nav">
    <a href="#">Whispers and the Racket Walking Tour</a>
    <a href="#">Desert Hop Trail</a>
    <a href="#">Calloway Row Stroll</a>
    <a href="#">Self Guided Tours</a>
    <a href="#">About</a>
    <a href="#">Contact</a>
  </nav>
  <div class="hero" role="img" aria-label="Night view of a glowing downtown Las Vegas street">
    <h1>Whispers and The Racket<br>Las Vegas Walking Tour</h1>
    <a class="btn" href="#">Book Now</a>
  </div>
  <section class="welcome">
    <h2 class="section-title">Welcome to Old Downtown</h2>
    <p class="body-text">Old downtown is where our walking tour begins, right in the heart of Las Vegas. During the tour, your guide will share spooky stories of local hotels, casino legends and the mob families who ran the town. Each tour stop is a chance to explore history, hear paranormal tales and snap a photo. Come along for an evening you will not soon forget.</p>
    <a class="btn" href="#">Book Now</a>
  </section>
  <div class="rule"></div>
  <section class="feature explore">
    <div class="map" role="img" aria-label="Illustrated map of downtown Las Vegas with tour stops"></div>
    <div class="feature-copy">
      <h2 class="section-title">Explore Downtown Las Vegas and hear the history of Calloway Row with a paranormal twist!</h2>
      <ul class="ticks">
        <li><svg viewBox="0 0 6 6"><circle cx="3" cy="3" r="3" fill="#e54698"/></svg>Visit 3 haunted Las Vegas properties and hear the real stories that made them so famous.</li>
        <li><svg viewBox="0 0 6 6"><circle cx="3" cy="3" r="3" fill="#e54698"/></svg>Highlights include the ghosts of mob bosses and tales from the old casino floors.</li>
        <li><svg viewBox="0 0 6 6"><circle cx="3" cy="3" r="3" fill="#e54698"/></svg>Explore historic downtown Las Vegas with an experienced guide on Calloway Row.</li>
      </ul>
    </div>
  </section>
  <div class="rule"></div>
  <section class="feature details">
    <div class="feature-copy">
      <h2 class="section-title">Details!</h2>
      <ul class="ticks">
        <li><svg viewBox="0 0 6 6"><circle cx="3" cy="3" r="3" fill="#e54698"/></svg>90 minute walking tour</li>
        <li><svg viewBox="0 0 6 6"><circle cx="3" cy="3" r="3" fill="#e54698"/></svg>Tour starts one hour before and ends at a nearby lounge.</li>
        <li><svg viewBox="0 0 6 6"><circle cx="3" cy="3" r="3" fill="#e54698"/></svg>Kids or adults are welcome, always spooky</li>
      </ul>
      <a class="btn" href="#">Book Now</a>
    </div>
    <div class="map" role="img" aria-label="Illustrated map of tour stops with location pins"></div>
  </section>
  <section class="app-promo">
    <h2>Whispers and The Racket Retold Self Guided Tour also on Neon Drifters App!</h2>
    <div class="store-badges"><span></span><span></span></div>
  </section>
  <footer class="site-footer">
    <nav class="footer-links">
      <a href="#">Whispers and the Racket Walking Tour</a>
      <a href="#">Desert Hop Trail</a>
      <a href="#">Calloway Row Stroll</a>
      <a href="#">Book Now</a>
      <a href="#">About Us</a>
      <a href="#">Contact</a>
      <a href="#">Privacy Policy</a>
    </nav>
    <div class="socials"><span></span><span></span><span></span><span></span><span></span><span></span></div>
    <p class="copyright">Copyright © 2021 Neon Drifters. All rights reserved.</p>
  </footer>
</section>

<section class="screen mobile">
  <header class="site-header">
    <div class="brand"><span class="brand-dot"></span>Neon Drifters</div>
    <div class="phone"><svg viewBox="0 0 10 10"><path d="M2 1l2 2-1 1.2a6 6 0 0 0 2.8 2.8L7 6l2 2-1.3 1.3C4.5 9 1 5.5.7 2.3z" fill="#e54698"/></svg>(702) 555-0148</div>
  </header>
  <nav class="main-nav">
    <a href="#">Walking Tour</a>
    <a href="#">Desert Hop Trail</a>
    <a href="#">Calloway Row Stroll</a>
    <a href="#">About</a>
    <a href="#">Contact</a>
  </nav>
  <div class="hero" role="img" aria-label="Night view of a glowing downtown Las Vegas street">
    <h1>Whispers and The Racket Las Vegas Walking Tour</h1>
    <a class="btn" href="#">Book Now</a>
  </div>
  <section class="welcome">
    <h2 class="section-title">Welcome to Old Downtown</h2>
    <p class="body-text">Old downtown is where our walking tour begins. Your guide will share spooky stories of local hotels, casino legends and mob families.</p>
    <a class="btn" href="#">Book Now</a>
  </section>
  <section class="feature explore">
    <h2 class="section-title">Explore Downtown Las Vegas and hear the history of Calloway Row with a paranormal twist!</h2>
    <div class="map" role="img" aria-label="Illustrated map of downtown Las Vegas with tour stops"></div>
    <ul class="ticks">
      <li><svg viewBox="0 0 6 6"><circle cx="3" cy="3" r="3" fill="#e54698"/></svg>Visit 3 haunted Las Vegas properties and hear their real stories.</li>
      <li><svg viewBox="0 0 6 6"><circle cx="3" cy="3" r="3" fill="#e54698"/></svg>Highlights include the ghosts of mob bosses.</li>
      <li><svg viewBox="0 0 6 6"><circle cx="3" cy="3" r="3" fill="#e54698"/></svg>Explore historic downtown with an experienced guide.</li>
    </ul>
  </section>
  <div class="rule"></div>
  <section class="feature details">
    <h2 class="section-title">Details!</h2>
    <div class="map" role="img" aria-label="Illustrated map of tour stops with location pins"></div>
    <ul class="ticks">
      <li><svg viewBox="0 0 6 6"><circle cx="3" cy="3" r="3" fill="#e54698"/></svg>90 minute walking tour</li>
      <li><svg viewBox="0 0 6 6"><circle cx="3" cy="3" r="3" fill="#e54698"/></svg>Tour starts and ends at a nearby lounge.</li>
      <li><svg viewBox="0 0 6 6"><circle cx="3" cy="3" r="3" fill="#e54698"/></svg>Kids or adults are welcome, always spooky</li>
    </ul>
    <a class="btn" href="#">Book Now</a>
  </section>
  <section class="app-promo">
    <h2>Whispers and The Racket Retold Self Guided Tour also on Neon Drifters App!</h2>
    <div class="store-badges"><span></span><span></span></div>
  </section>
  <footer class="site-footer">
    <nav class="footer-links">
      <a href="#">Whispers and the Racket Walking Tour</a>
      <a href="#">Desert Hop Trail</a>
      <a href="#">Calloway Row Stroll</a>
      <a href="#">Book Now</a>
      <a href="#">Contact</a>
    </nav>
    <div class="socials"><span></span><span></span><span></span><span></span><span></span></div>
    <p class="copyright">Copyright © 2021 Neon Drifters. All rights reserved.</p>
  </footer>
</section>

</body>
</html>
```